Copper Ridge Inquiries Letterhead

I would like to design a letterhead for a private investigation company. Our primary clients will be law firms. The business card is included below

```html
<!DOCTYPE html>
<html lang="en">
<head>
<meta charset="utf-8">
<title>Copper Ridge Inquiries Letterhead</title>
<link rel="stylesheet" href="https://fonts.googleapis.com/css2?family=Montserrat:wght@400;500;800&family=Lato:wght@400;700&family=Italianno&display=swap">
<style>
  :root {
    --backdrop: #e6e6e6;
    --paper: #ffffff;
    --accent: #ee5a2a;
    --navy: #1d2f5c;
    --ink: #1a1a1a;
    --muted: #333333;
  }
  * { margin: 0; padding: 0; box-sizing: border-box; }
  html, body { width: 1200px; height: 1079px; overflow: hidden; background: var(--backdrop); }
  .letterhead {
    position: absolute; left: 232px; top: 20px; width: 735px; height: 1040px;
    background: var(--paper); box-shadow: 0 4px 18px rgba(0,0,0,.18);
    font-family: "Lato", sans-serif; color: var(--ink);
  }
  .brand { position: absolute; left: 37px; top: 110px; display: flex; align-items: center; gap: 10px; }
  .brand-dot { width: 26px; height: 26px; border-radius: 50%; background: var(--accent); }
  .brand-name {
    font-family: "Montserrat", sans-serif; font-weight: 800; font-size: 19px;
    color: var(--navy); letter-spacing: .3px; line-height: 1.15; text-transform: uppercase;
  }
  .divider { position: absolute; left: 334px; top: 95px; width: 1.5px; height: 72px; background: var(--accent); }
  .contact {
    position: absolute; left: 366px; top: 91px; list-style: none;
    font-family: "Montserrat", sans-serif; font-size: 12.5px; color: var(--muted); text-transform: uppercase;
  }
  .contact li { display: flex; align-items: center; gap: 7px; height: 18.5px; }
  .contact svg { width: 11px; height: 11px; fill: var(--accent); flex: none; }
  .contact .license { margin-top: 7px; margin-left: -2px; }
  .rule { position: absolute; left: 37px; width: 661px; height: 1.5px; background: var(--accent); }
  .rule.top { top: 228px; }
  .rule.bottom { top: 981px; }
  .letter { position: absolute; left: 37px; top: 300px; width: 661px; font-size: 14.3px; line-height: 17.5px; }
  .date { margin-bottom: 18px; }
  .recipient { margin-bottom: 17px; }
  .address { margin-bottom: 22px; }
  .salutation { font-weight: 700; font-size: 18px; margin-bottom: 22px; }
  .body p { text-align: justify; font-size: 14px; line-height: 16.1px; margin-bottom: 17px; }
  .closing { margin-top: 36px; }
  .signature {
    position: absolute; left: 37px; top: 888px;
    font-family: "Italianno", cursive; font-size: 42px; color: var(--ink);
  }
  .tagline {
    position: absolute; top: 999px; left: 0; width: 100%; text-align: center;
    font-family: "Montserrat", sans-serif; font-size: 12.5px; color: var(--muted); text-transform: uppercase;
  }
</style>
</head>
<body>
<main class="letterhead">
  <header>
    <div class="brand">
      <span class="brand-dot"></span>
      <span class="brand-name">Copper Ridge<br>Inquiries</span>
    </div>
    <div class="divider"></div>
    <ul class="contact">
      <li><svg viewBox="0 0 12 12"><path d="M6 0a4 4 0 0 0-4 4c0 3 4 8 4 8s4-5 4-8a4 4 0 0 0-4-4zm0 5.6A1.6 1.6 0 1 1 6 2.4a1.6 1.6 0 0 1 0 3.2z"/></svg>Cedar Falls, TX</li>
      <li><svg viewBox="0 0 12 12"><path d="M1 5c0-2 2-3 5-3s5 1 5 3v1H8.5V4.5h-5V6H1zM3 6.5h6L10.5 10h-9z"/></svg>555.014.2287</li>
      <li><svg viewBox="0 0 12 12"><path d="M1 2.5h10v7H1zM1.6 3l4.4 3.4L10.4 3v1L6 7.4 1.6 4z" fill-rule="evenodd"/></svg>dana@copperridgeinquiries.com</li>
      <li class="license">License No. 04472916</li>
    </ul>
  </header>
  <div class="rule top"></div>

  <article class="letter">
    <p class="date">January-03-2020</p>
    <p class="recipient">Mr, Tobin Hallery<br>President</p>
    <p class="address">Harbor Lane Group<br>123 Street Name, Suite# 10<br>City, State, 120023</p>
    <p class="salutation">Dear Mr, Tobin</p>
    <div class="body">
      <p>Lorem ipsum dolor sit amet, consectetur adipiscing elit, sed do eiusmod tempor incididunt ut labore et dolore magna aliqua. Ut enim ad minim veniam, quis nostrud exercitation ullamco laboris nisi ut aliquip ex ea commodo consequat. Duis aute irure dolor in reprehenderit in voluptate velit esse cillum dolore eu fugiat nulla pariatur.</p>
      <p>Lorem ipsum dolor sit amet, consectetur adipiscing elit, sed do eiusmod tempor incididunt ut labore et dolore magna aliqua. Ut enim ad minim veniam, quis nostrud exercitation ullamco laboris nisi ut aliquip ex ea commodo consequat. Duis aute irure dolor in reprehenderit in voluptate velit esse cillum dolore eu fugiat nulla pariatur.</p>
      <p>Lorem ipsum dolor sit amet, consectetur adipiscing elit, sed do eiusmod tempor incididunt ut labore et dolore magna aliqua. Ut enim ad minim veniam, quis nostrud exercitation ullamco laboris nisi ut aliquip ex ea commodo consequat.</p>
      <p>Excepteur sint occaecat cupidatat non proident, sunt in culpa qui officia deserunt mollit anim id est laborum. re et dolore magnam aliquam quaerat voluptatem.</p>
    </div>
    <p class="closing">Regards</p>
  </article>
  <p class="signature">Elena Marsh</p>

  <div class="rule bottom"></div>
  <footer class="tagline">Over 20 years of investigative experince</footer>
</main>
</body>
</html>
```